professional business card design for technology company

We are a small technology consulting firm, specialising in consulting based around Cloud and Managed services. Our colour scheme is yellow, blue and white, as you can see in the logos. Although we are based in melbourne australia, due to the nature of our work, our clients can be located anywhere. We are looking for a clean, professional, positive look - similar to our company logo

Target Market(s)

small business

Industry/Entity Type

Business

Contact Information for Business Card

eye catching, designed to incorporate some level of raised printing. Must contain website address, phone number, name and job title

Requirements
Must have
• Logo (attached) - use of the same colour scheme

```html
<!DOCTYPE html>
<html lang="en">
<head>
<meta charset="utf-8">
<title>Nuvessar Business Card</title>
<link rel="stylesheet" href="https://fonts.googleapis.com/css2?family=Exo+2:wght@400;500;600;700&display=swap">
<style>
  :root {
    --backdrop: #e9ebee;
    --card: #ffffff;
    --band: #38abe0;
    --ink: #2e3b4e;
    --text: #3c3c3c;
    --icon: #585858;
    --divider: #5a5a5a;
  }
  * { margin: 0; padding: 0; box-sizing: border-box; }
  html, body { width: 1200px; height: 817px; overflow: hidden; background: var(--backdrop); }
  body { font-family: "Exo 2", sans-serif; color: var(--text); position: relative; }

  .card {
    position: absolute; left: 110px; top: 118px; width: 980px; height: 580px;
    background: var(--card); border-radius: 44px; overflow: hidden;
    box-shadow: 0 10px 30px rgba(0,0,0,.12);
  }
  .band { position: absolute; left: 0; width: 100%; background: var(--band); }
  .band--top { top: 110px; height: 40px; }
  .band--name { top: 218px; height: 44px; }
  .band--address { top: 498px; height: 46px; }

  .brand {
    position: absolute; left: 50%; top: 62px; transform: translateX(-50%);
    display: flex; align-items: center; gap: 18px;
    background: var(--card); padding: 12px 28px;
    white-space: nowrap;
  }
  .brand__dot { width: 58px; height: 58px; border-radius: 50%; background: var(--band); flex: none; }
  .brand__name { font-size: 64px; font-weight: 700; color: var(--icon); line-height: 1; }

  .identity {
    position: absolute; left: 64px; top: 218px; height: 44px;
    display: flex; align-items: center; gap: 14px; white-space: nowrap;
  }
  .identity__name { font-size: 27px; font-weight: 500; letter-spacing: 1.5px; color: var(--ink); }
  .identity__sep { width: 3px; height: 24px; background: var(--ink); }
  .identity__title { font-size: 17px; font-weight: 500; letter-spacing: 1.5px; color: var(--ink); }

  .contacts {
    position: absolute; left: 0; top: 290px; width: 100%; height: 184px;
    display: flex; align-items: stretch;
  }
  .contact {
    flex: 1; display: flex; flex-direction: column; align-items: center;
    justify-content: center; gap: 22px; white-space: nowrap;
  }
  .contact + .contact { border-left: 3px solid var(--divider); }
  .contact__icon { width: 72px; height: 72px; }
  .contact__value { font-size: 26px; font-weight: 500; letter-spacing: 1px; color: var(--text); }
  .contact--phone .contact__value { font-size: 30px; letter-spacing: 2px; }

  .address {
    position: absolute; left: 40px; top: 498px; height: 46px;
    display: flex; align-items: center; gap: 12px; white-space: nowrap;
  }
  .address__text { font-size: 21px; font-weight: 500; letter-spacing: 2px; color: var(--ink); }
</style>
</head>
<body>
  <main class="card">
    <div class="band band--top"></div>
    <div class="band band--name"></div>
    <div class="band band--address"></div>

    <header class="brand">
      <span class="brand__dot"></span>
      <span class="brand__name">Nuvessar</span>
    </header>

    <div class="identity">
      <svg width="28" height="32" viewBox="0 0 28 32" aria-hidden="true">
        <circle cx="14" cy="9" r="8" fill="var(--ink)"/>
        <path d="M0 32 C0 22 6 18 14 18 C22 18 28 22 28 32 Z" fill="var(--ink)"/>
      </svg>
      <span class="identity__name">MARCUS HALE</span>
      <span class="identity__sep"></span>
      <span class="identity__title">GENERAL MANAGER</span>
    </div>

    <section class="contacts">
      <div class="contact contact--phone">
        <svg class="contact__icon" viewBox="0 0 72 72" aria-hidden="true">
          <circle cx="36" cy="36" r="36" fill="var(--icon)"/>
          <rect x="25" y="15" width="22" height="42" rx="4" fill="#fff"/>
          <rect x="28" y="20" width="16" height="28" fill="var(--icon)"/>
          <circle cx="36" cy="52" r="2.2" fill="var(--icon)"/>
        </svg>
        <span class="contact__value">012 555 0148</span>
      </div>
      <div class="contact contact--email">
        <svg class="contact__icon" viewBox="0 0 72 72" aria-hidden="true">
          <circle cx="36" cy="36" r="36" fill="var(--icon)"/>
          <rect x="17" y="23" width="38" height="26" fill="#fff"/>
          <path d="M17 23 L36 39 L55 23" fill="none" stroke="var(--icon)" stroke-width="2.5"/>
        </svg>
        <span class="contact__value">hello@nuvessar.com</span>
      </div>
      <div class="contact contact--web">
        <svg class="contact__icon" viewBox="0 0 72 72" aria-hidden="true">
          <circle cx="36" cy="36" r="36" fill="var(--icon)"/>
          <g fill="none" stroke="#fff" stroke-width="2.5">
            <circle cx="36" cy="36" r="19"/>
            <ellipse cx="36" cy="36" rx="8" ry="19"/>
            <line x1="17" y1="36" x2="55" y2="36"/>
            <line x1="36" y1="17" x2="36" y2="55"/>
            <line x1="20" y1="27" x2="52" y2="27"/>
            <line x1="20" y1="45" x2="52" y2="45"/>
          </g>
        </svg>
        <span class="contact__value">www.nuvessar.com</span>
      </div>
    </section>

    <div class="address">
      <svg width="20" height="28" viewBox="0 0 20 28" aria-hidden="true">
        <path d="M10 0 C4.5 0 0 4.5 0 10 C0 17 10 28 10 28 C10 28 20 17 20 10 C20 4.5 15.5 0 10 0 Z" fill="var(--ink)"/>
        <circle cx="10" cy="10" r="4" fill="var(--band)"/>
      </svg>
      <span class="address__text">214,9th floor,Harbour View Road MEL</span>
    </div>
  </main>
</body>
</html>
```